Business Card Design For Marketing Agnecy LVP

Need business card design for marketing agency.

Doug Fenwick
President, CEO
1-555-302-4196
doug@boldpromoperksgroup.example
www.BoldPromoPerksGroup.example

Back Side:
Boost Sales Using Rewards, Incentives & Giveaways
Get A Free Sample Package

Target Market(s)

B2B

Industry/Entity Type

Marketing

Contact Information for Business Card

Doug Fenwick
President, CEO
1-555-302-4196

Back Side:
Get A Free Sample Package

Please note that my current url is OLD DESIGN. I am working on new design and want the business card to match color themes at least on new site. Here is the demo link for new site so you can see the colors I use, etc.

http://layoutcratehub.example/kq/doug/lvp_final/index.html

Requirements
Must have
• Please note that my current url is OLD DESIGN. I am working on new design and want the business card to match color themes at least on new site. Here is the demo link for new site so you can see the colors I use, etc.

Nice to have

Should not have

```html
<!DOCTYPE html>
<html lang="en">
<head>
<meta charset="UTF-8">
<title>LVP Business Card</title>
<link href="https://fonts.googleapis.com/css2?family=Montserrat:wght@400;500;600;700;800&display=swap" rel="stylesheet">
<style>
  :root {
    --backdrop: #2b2b2d;
    --card-black: #121214;
    --card-dark: #18191c;
    --gloss: #2c2c30;
    --brand-blue: #2f7fd1;
    --brand-blue-deep: #1f5fae;
    --brand-green: #5cc23a;
    --white: #ffffff;
    --muted: #c9ccd2;
  }
  * { margin: 0; padding: 0; box-sizing: border-box; }
  html, body { width: 800px; height: 1200px; overflow: hidden; }
  body {
    background: var(--backdrop);
    font-family: "Montserrat", sans-serif;
    position: relative;
  }
  .card {
    position: absolute;
    left: 80px;
    width: 640px;
    height: 366px;
    border-radius: 4px;
    overflow: hidden;
    box-shadow: 0 14px 30px rgba(0,0,0,0.45);
  }
  .card-front { top: 150px; background: var(--card-black); }
  .card-back { top: 680px; background: var(--card-dark); }

  .front-brand {
    position: absolute;
    left: 0; right: 0; top: 96px;
    text-align: center;
    color: var(--gloss);
    font-weight: 800;
  }
  .front-brand .mark { font-size: 92px; line-height: 1; letter-spacing: 2px; }
  .front-brand .name { font-size: 22px; letter-spacing: 3px; margin-top: 8px; }

  .back-brand {
    position: absolute;
    left: 250px; top: 42px;
    color: var(--brand-blue);
    font-weight: 800;
    display: flex;
    align-items: center;
    gap: 12px;
  }
  .back-brand .mark { font-size: 44px; line-height: 1; }
  .back-brand .name { font-size: 16px; letter-spacing: 1.5px; line-height: 1.2; }

  .person {
    position: absolute;
    left: 36px; top: 160px;
  }
  .person-name { color: var(--brand-blue); font-size: 19px; font-weight: 600; }
  .person-title { color: var(--muted); font-size: 11px; font-weight: 500; margin-top: 4px; }

  .contact-list {
    position: absolute;
    left: 286px; top: 160px;
    list-style: none;
  }
  .contact-list li {
    display: flex; align-items: center; gap: 10px;
    color: var(--white);
    font-size: 11px;
    font-weight: 500;
    margin-bottom: 10px;
  }
  .contact-list svg { width: 13px; height: 13px; flex: none; }

  .accent-line {
    position: absolute;
    left: 0; top: 282px;
    width: 200px; height: 7px;
    background: var(--brand-green);
  }
  .cta-band {
    position: absolute;
    right: 0; bottom: 0;
    width: 470px; height: 78px;
  }
  .cta-band svg { position: absolute; inset: 0; }
  .cta-text {
    position: absolute;
    right: 30px; bottom: 26px;
    color: var(--white);
    font-size: 15px;
    font-weight: 800;
    letter-spacing: 0.8px;
    text-transform: uppercase;
  }
</style>
</head>
<body>

<section class="card card-front">
  <div class="front-brand">
    <div class="mark">LVP</div>
    <div class="name">BOLD PROMO PERKS GROUP</div>
  </div>
</section>

<section class="card card-back">
  <div class="back-brand">
    <div class="mark">LVP</div>
    <div class="name">BOLD PROMO<br>PERKS GROUP</div>
  </div>

  <div class="person">
    <div class="person-name">Doug Fenwick</div>
    <div class="person-title">President, CEO</div>
  </div>

  <ul class="contact-list">
    <li>
      <svg viewBox="0 0 24 24" fill="#c9ccd2"><path d="M6.6 10.8a15 15 0 0 0 6.6 6.6l2.2-2.2a1 1 0 0 1 1-.25 11.4 11.4 0 0 0 3.6.57 1 1 0 0 1 1 1V20a1 1 0 0 1-1 1A17 17 0 0 1 3 4a1 1 0 0 1 1-1h3.5a1 1 0 0 1 1 1c0 1.25.2 2.45.57 3.57a1 1 0 0 1-.25 1z"/></svg>
      1-555-302-4196
    </li>
    <li>
      <svg viewBox="0 0 24 24" fill="#c9ccd2"><path d="M3 5h18v14H3z" fill="none" stroke="#c9ccd2" stroke-width="2"/><path d="M3 6l9 7 9-7" fill="none" stroke="#c9ccd2" stroke-width="2"/></svg>
      doug@boldpromoperksgroup.example
    </li>
    <li>
      <svg viewBox="0 0 24 24" fill="none" stroke="#c9ccd2" stroke-width="2"><circle cx="12" cy="12" r="9"/><path d="M3 12h18M12 3c3 3.5 3 14.5 0 18M12 3c-3 3.5-3 14.5 0 18"/></svg>
      www.BoldPromoPerksGroup.example
    </li>
  </ul>

  <div class="accent-line"></div>

  <div class="cta-band">
    <svg viewBox="0 0 470 78" preserveAspectRatio="none">
      <polygon points="40,0 470,0 470,78 0,78" fill="#2f7fd1"/>
      <polygon points="40,0 470,0 470,6 37,6" fill="#1f5fae"/>
    </svg>
    <div class="cta-text">Get a free sample package</div>
  </div>
</section>

</body>
</html>
```